Delivery Performance Dashboard for Web Portal

We need you to design a dashboard for our web portal. We deliver sand and stone to construction jobsites. The attached screenshot is from our current web portal dashboard . It shows how much material has been delivered from an order.

Dump trucks will deliver multiple loads during the day and the dispatcher uses the dashboard to monitor if they need to add more trucks or less trucks to fulfill the order. An example would be, I need to ship 1,000 tons of sand to a jobsite and I plan to use 10 trucks during the day and that it will take 10 hours of hauling to complete the job. After 5 hours of hauling (50% the day is over), I should have delivered 500 tons of sand (50% of the order). But maybe there is a lot of traffic, and I only have delivered 300 tons. The dashboard will show that I am behind schedule and I might need to add 2 more trucks to the job.

Industry/Entity Type

Construction

Font styles to use
Sans Serif

Requirements
Must have
• We need a progress bar showing how much material has been delivered, how much material was requested to be delivered total and how much material should have been delivered at the current time. The goal is to show the user if the deliveries are ahead or behind the expected pace and why.
Nice to have
• The icons for plant, driving and jobsite show if the actual times have exceeded or beaten the planned times. Maybe you have other ideas to show the user if the trucks are sitting longer on the jobsite, at the plant to get loaded or driving to and from the jobsite.

```html
<!DOCTYPE html>
<html lang="en">
<head>
<meta charset="utf-8">
<title>Delivery Dashboard</title>
<link href="https://fonts.googleapis.com/css2?family=Lato:wght@400;700;900&display=swap" rel="stylesheet">
<style>
:root{
  --sidebar:#2f74b5;
  --logo-bg:#232323;
  --page:#f6f6f6;
  --white:#ffffff;
  --ink:#1d1d1d;
  --muted:#3a3a3a;
  --brand:#2b75bf;
  --track:#e8e8e8;
  --orange:#f7a600;
  --green:#5aa215;
  --cyan:#1aa3d4;
  --pink:#e8266e;
  --badge:#f7b500;
  --row-alt:#f4f4f4;
  --line:#dcdcdc;
  --bar-done:#2f74b5;
  --bar-left:#4a4a4a;
  --up:#e0262b;
  --down:#5aa215;
}
*{box-sizing:border-box;margin:0;padding:0}
html,body{width:1200px;height:744px;overflow:hidden;background:var(--page)}
body{font-family:"Lato",sans-serif;color:var(--ink)}
.stage{position:absolute;left:0;top:0;width:1935px;height:1200px;transform:scale(0.62016);transform-origin:0 0;background:var(--page)}
.abs{position:absolute}

/* sidebar */
.sidebar{left:0;top:0;width:215px;height:1200px;background:var(--sidebar);color:var(--white)}
.logo{left:0;top:0;width:215px;height:89px;background:var(--logo-bg);display:flex;align-items:center;justify-content:center;font-size:26px;font-weight:400;letter-spacing:.5px;color:var(--white)}
.nav{position:absolute;left:0;top:110px;width:215px}
.nav-item{position:relative;height:55px;display:flex;align-items:center;padding-left:86px;font-size:14.5px;font-weight:700;text-transform:uppercase}
.nav-item svg{position:absolute;left:38px;top:50%;transform:translateY(-50%)}
.nav-item::after{content:"";position:absolute;left:42px;right:0;bottom:0;border-bottom:1px dashed rgba(255,255,255,.55)}
.nav-item.active{height:38px;margin-bottom:17px;margin-left:33px;padding-left:53px;background:var(--white);color:var(--sidebar);border-radius:19px 0 0 19px}
.nav-item.active svg{left:9px}
.nav-item.active::after{display:none}
.copyright{left:36px;top:1122px;font-size:13.5px;line-height:22px}

/* top bar */
.search{left:250px;top:20px;width:711px;height:50px;background:var(--white);border:1px solid #cfcfcf;font-size:17px;color:#444;padding:0 18px;display:flex;align-items:center;justify-content:space-between}
.top-icon{top:28px}
.badge{position:absolute;top:-4px;right:-8px;width:15px;height:15px;border-radius:50%;background:var(--badge);color:var(--white);font-size:10px;font-weight:700;text-align:center;line-height:15px}
.avatar{left:1728px;top:22px;width:46px;height:46px;border-radius:50%;background:linear-gradient(160deg,#b9b3ad,#5f5a56)}
.user{left:1789px;top:36px;font-size:13.5px;font-weight:700}

/* stat cards */
.stat{top:132px;width:388px;height:182px;background:var(--white);border-radius:12px;box-shadow:0 2px 10px rgba(0,0,0,.08)}
.stat h2{position:absolute;left:29px;top:58px;font-size:30px;font-weight:700;color:var(--brand);letter-spacing:.3px}
.stat p{position:absolute;left:29px;top:100px;font-size:15.5px;color:var(--muted)}
.stat svg{position:absolute;left:226px;top:18px}
.ring-value{font-family:"Lato",sans-serif;font-size:52px;font-weight:900;fill:var(--ink)}

/* deliveries table */
.orders{left:250px;top:377px;width:1645px;height:274px;background:var(--white);border:1px solid #c9c9c9;border-radius:12px;overflow:hidden;box-shadow:0 2px 8px rgba(0,0,0,.08)}
.orders table{width:100%;border-collapse:collapse;table-layout:fixed}
.orders th{height:55px;background:#f2f2f2;font-size:14.5px;font-weight:700;text-align:left;padding-left:22px;text-transform:uppercase;border-right:1px solid var(--line);border-bottom:1px solid var(--line)}
.orders td{height:52px;font-size:14.5px;padding-left:21px;border-right:1px solid var(--line);white-space:nowrap}
.orders th:last-child,.orders td:last-child{border-right:none}
.orders tr.alt td{background:var(--row-alt)}
.orders tr.empty td{height:57px;background:var(--row-alt)}
.sort{display:inline-block;margin-left:18px;vertical-align:middle}
.tons{padding-right:28px}
.tons-bar{height:6px;border-radius:3px;background:var(--bar-left);overflow:hidden;margin-top:4px}
.tons-bar span{display:block;height:100%;background:var(--bar-done)}
.tons-meta{display:flex;justify-content:space-between;font-size:13.5px;margin-top:7px}
.waits{display:flex;align-items:center;gap:5px}
.ahead{color:var(--green)}
.behind{color:var(--up)}

/* bottom panels */
.panel{top:706px;width:529px;height:406px;background:var(--white);border-radius:12px;box-shadow:0 2px 10px rgba(0,0,0,.08)}
.panel h3{height:73px;border-bottom:1px solid #d6d6d6;font-size:27px;font-weight:700;padding:22px 0 0 27px}
.map{position:absolute;left:27px;top:110px;width:474px;height:270px;border-radius:6px;background:linear-gradient(180deg,#2d6aa3 0%,#1a3f63 55%,#08131f 100%)}
.chart{position:absolute;left:0;top:73px}
.notes{padding:17px 28px 0}
.note h4{font-size:19px;font-weight:700;color:var(--brand);margin-bottom:6px}
.note p{font-size:16px;line-height:27px;color:#222;margin-bottom:22px}
</style>
</head>
<body>
<div class="stage">

  <aside class="abs sidebar">
    <div class="abs logo">LOGO GOES HERE</div>
    <nav class="nav">
      <div class="nav-item active">
        <svg width="32" height="20" viewBox="0 0 32 20"><path d="M3 18a13 13 0 0 1 26 0" fill="none" stroke="currentColor" stroke-width="4"/><path d="M16 17 24 6" stroke="currentColor" stroke-width="3"/></svg>Dashboard</div>
      <div class="nav-item">
        <svg width="26" height="22" viewBox="0 0 26 22"><rect x="1" y="5" width="24" height="16" rx="2" fill="#fff"/><rect x="8" y="1" width="10" height="6" fill="none" stroke="#fff" stroke-width="2"/><path d="M7 5v16M19 5v16" stroke="#2f74b5" stroke-width="2"/></svg>Delivery</div>
      <div class="nav-item">
        <svg width="28" height="22" viewBox="0 0 28 22"><rect x="9" y="2" width="18" height="14" fill="#fff"/><path d="M1 8h7v8H1z" fill="#fff"/><circle cx="6" cy="18" r="3" fill="#fff"/><circle cx="21" cy="18" r="3" fill="#fff"/></svg>Dump Truck</div>
      <div class="nav-item">
        <svg width="28" height="22" viewBox="0 0 28 22"><path d="M2 2v18h24" fill="none" stroke="#fff" stroke-width="2"/><path d="M5 16l7-7 5 4 8-8" fill="none" stroke="#fff" stroke-width="2.5"/></svg>Reports</div>
      <div class="nav-item">
        <svg width="22" height="26" viewBox="0 0 22 26"><path d="M1 1h14l6 6v18H1z" fill="#fff"/><path d="M5 12h12M5 16h12M5 20h12" stroke="#2f74b5" stroke-width="2"/></svg>Documents</div>
      <div class="nav-item">
        <svg width="24" height="24" viewBox="0 0 24 24"><circle cx="12" cy="12" r="8" fill="none" stroke="#fff" stroke-width="5" stroke-dasharray="3.5 2.8"/><circle cx="12" cy="12" r="6" fill="#fff"/><circle cx="12" cy="12" r="3" fill="#2f74b5"/></svg>Settings</div>
      <div class="nav-item">
        <svg width="24" height="24" viewBox="0 0 24 24"><circle cx="12" cy="12" r="11" fill="#fff"/><text x="12" y="17" text-anchor="middle" font-family="Lato,sans-serif" font-weight="900" font-size="15" fill="#2f74b5">?</text></svg>Help</div>
    </nav>
    <div class="abs copyright">© 2020 Company Name<br>All Rights Reserved.</div>
  </aside>

  <div class="abs search">Search...
    <svg width="20" height="20" viewBox="0 0 20 20"><circle cx="8" cy="8" r="6" fill="none" stroke="#2f74b5" stroke-width="3"/><path d="M12.5 12.5 18 18" stroke="#2f74b5" stroke-width="3"/></svg>
  </div>
  <div class="abs top-icon" style="left:1611px">
    <svg width="20" height="22" viewBox="0 0 20 22"><circle cx="10" cy="6" r="5" fill="#2f74b5"/><path d="M1 22a9 9 0 0 1 18 0z" fill="#2f74b5"/></svg>
    <span class="badge">0</span>
  </div>
  <div class="abs top-icon" style="left:1672px">
    <svg width="20" height="22" viewBox="0 0 20 22"><path d="M10 1a6 6 0 0 1 6 6v6l3 4H1l3-4V7a6 6 0 0 1 6-6z" fill="#2f74b5"/><circle cx="10" cy="20" r="2.5" fill="#2f74b5"/></svg>
    <span class="badge">0</span>
  </div>
  <div class="abs avatar" role="img" aria-label="User profile photo"></div>
  <div class="abs user">Dana Morrow <svg width="10" height="7" viewBox="0 0 10 7"><path d="M1 1l4 4 4-4" fill="none" stroke="#222" stroke-width="1.6"/></svg></div>

  <section class="abs stat" style="left:250px">
    <h2>Vestibulum</h2><p>Ante ipsum</p>
    <svg width="144" height="144" viewBox="0 0 144 144"><circle cx="72" cy="72" r="68" fill="none" stroke="var(--track)" stroke-width="5"/><circle cx="72" cy="72" r="68" fill="none" stroke="var(--orange)" stroke-width="6" stroke-dasharray="107 428" transform="rotate(-90 72 72)"/><text class="ring-value" x="72" y="90" text-anchor="middle">25</text></svg>
  </section>
  <section class="abs stat" style="left:669px">
    <h2>Vestibulum</h2><p>Ante ipsum</p>
    <svg width="144" height="144" viewBox="0 0 144 144"><circle cx="72" cy="72" r="68" fill="none" stroke="var(--track)" stroke-width="5"/><circle cx="72" cy="72" r="68" fill="none" stroke="var(--green)" stroke-width="6" stroke-dasharray="171 428" transform="rotate(-90 72 72)"/><text class="ring-value" x="72" y="90" text-anchor="middle">40</text></svg>
  </section>
  <section class="abs stat" style="left:1088px">
    <h2>Vestibulum</h2><p>Ante ipsum</p>
    <svg width="144" height="144" viewBox="0 0 144 144"><circle cx="72" cy="72" r="68" fill="none" stroke="var(--track)" stroke-width="5"/><circle cx="72" cy="72" r="68" fill="none" stroke="var(--cyan)" stroke-width="6" stroke-dasharray="107 428" transform="rotate(-90 72 72)"/><text class="ring-value" x="72" y="90" text-anchor="middle">25</text></svg>
  </section>
  <section class="abs stat" style="left:1507px">
    <h2>Vestibulum</h2><p>Ante ipsum</p>
    <svg width="144" height="144" viewBox="0 0 144 144"><circle cx="72" cy="72" r="68" fill="none" stroke="var(--track)" stroke-width="5"/><circle cx="72" cy="72" r="68" fill="none" stroke="var(--pink)" stroke-width="6" stroke-dasharray="363 428" transform="rotate(-90 72 72)"/><text class="ring-value" x="72" y="90" text-anchor="middle">85</text></svg>
  </section>

  <section class="abs orders">
    <table>
      <colgroup><col style="width:123px"><col style="width:191px"><col style="width:223px"><col style="width:281px"><col style="width:123px"><col style="width:320px"><col style="width:142px"><col style="width:144px"><col style="width:97px"></colgroup>
      <thead>
        <tr>
          <th>Order<svg class="sort" width="9" height="13" viewBox="0 0 9 13"><path d="M4.5 0 9 5H0zM4.5 13 0 8h9z" fill="#222"/></svg></th>
          <th>Origin<svg class="sort" width="9" height="13" viewBox="0 0 9 13"><path d="M4.5 0 9 5H0zM4.5 13 0 8h9z" fill="#222"/></svg></th>
          <th>Destination<svg class="sort" width="9" height="13" viewBox="0 0 9 13"><path d="M4.5 0 9 5H0zM4.5 13 0 8h9z" fill="#222"/></svg></th>
          <th>Customer<svg class="sort" width="9" height="13" viewBox="0 0 9 13"><path d="M4.5 0 9 5H0zM4.5 13 0 8h9z" fill="#222"/></svg></th>
          <th>Status<svg class="sort" width="9" height="13" viewBox="0 0 9 13"><path d="M4.5 0 9 5H0zM4.5 13 0 8h9z" fill="#222"/></svg></th>
          <th style="padding-left:17px">Tons</th>
          <th>Wait Times</th>
          <th><svg width="12" height="12" viewBox="0 0 12 12"><circle cx="6" cy="6" r="5" fill="none" stroke="#222" stroke-width="1.6"/><path d="M6 3v3h2" fill="none" stroke="#222" stroke-width="1.4"/></svg> Remaining</th>
          <th>+/- <svg width="15" height="11" viewBox="0 0 15 11"><rect x="4" y="0" width="11" height="7" fill="#222"/><rect x="0" y="3" width="4" height="4" fill="#222"/><circle cx="3" cy="9" r="2" fill="#222"/><circle cx="12" cy="9" r="2" fill="#222"/></svg></th>
        </tr>
      </thead>
      <tbody>
        <tr>
          <td>17746</td><td>Ridgeway Asphalt Plant</td><td>BZJV -185 from mm 77 - 98</td><td>Granton Construction - North Division</td><td>Accepted</td>
          <td class="tons" style="padding-left:17px"><div class="tons-bar"><span style="width:61%"></span></div><div class="tons-meta"><span>722.57 / 1500</span><span>7:30am - 5:00pm</span></div></td>
          <td><div class="waits">
            <svg width="12" height="11" viewBox="0 0 12 11"><path d="M0 11V4l4 2V4l4 2V0h4v11z" fill="#222"/></svg>
            <svg width="8" height="6" viewBox="0 0 8 6"><path d="M4 0 8 6H0z" fill="var(--up)"/></svg>
            <svg width="15" height="11" viewBox="0 0 15 11"><rect x="4" width="11" height="7" fill="#222"/><rect y="3" width="4" height="4" fill="#222"/><circle cx="3" cy="9" r="2" fill="#222"/><circle cx="12" cy="9" r="2" fill="#222"/></svg>
            <svg width="8" height="6" viewBox="0 0 8 6"><path d="M4 0 8 6H0z" fill="var(--down)"/></svg>
            <svg width="9" height="13" viewBox="0 0 9 13"><path d="M4.5 13 1 6a4 4 0 1 1 7 0z" fill="#222"/><circle cx="4.5" cy="4.5" r="1.6" fill="#fff"/></svg>
            <svg width="8" height="6" viewBox="0 0 8 6"><path d="M0 0h8L4 6z" fill="var(--down)"/></svg>
          </div></td>
          <td class="ahead">+1:25 hrs</td><td class="behind">-31</td>
        </tr>
        <tr class="alt">
          <td>17747</td><td>Millbrook Asphalt Plant</td><td>Cedar Hollow</td><td>Granton Construction - North Division</td><td>Accepted</td>
          <td class="tons" style="padding-left:17px"><div class="tons-bar"><span style="width:100%"></span></div><div class="tons-meta"><span>722.57 / 1500</span><span>7:30am - 5:00pm</span></div></td>
          <td><div class="waits">
            <svg width="12" height="11" viewBox="0 0 12 11"><path d="M0 11V4l4 2V4l4 2V0h4v11z" fill="#222"/></svg>
            <svg width="8" height="6" viewBox="0 0 8 6"><path d="M4 0 8 6H0z" fill="var(--up)"/></svg>
            <svg width="15" height="11" viewBox="0 0 15 11"><rect x="4" width="11" height="7" fill="#222"/><rect y="3" width="4" height="4" fill="#222"/><circle cx="3" cy="9" r="2" fill="#222"/><circle cx="12" cy="9" r="2" fill="#222"/></svg>
            <svg width="8" height="6" viewBox="0 0 8 6"><path d="M0 0h8L4 6z" fill="var(--down)"/></svg>
            <svg width="9" height="13" viewBox="0 0 9 13"><path d="M4.5 13 1 6a4 4 0 1 1 7 0z" fill="#222"/><circle cx="4.5" cy="4.5" r="1.6" fill="#fff"/></svg>
            <svg width="8" height="6" viewBox="0 0 8 6"><path d="M0 0h8L4 6z" fill="var(--down)"/></svg>
          </div></td>
          <td class="behind">-0:28 hrs</td><td class="ahead">+16</td>
        </tr>
        <tr>
          <td>17794</td><td>Ridgeway Asphalt Plant</td><td>BZJV -185 from mm 77 - 98</td><td>Granton Construction - North Division</td><td>Accepted</td>
          <td class="tons" style="padding-left:17px"><div class="tons-bar"><span style="width:0"></span></div><div class="tons-meta"><span>722.57 / 1500</span><span>7:30am - 5:00pm</span></div></td>
          <td style="padding-left:38px"><div class="waits">
            <span class="ahead">-</span>
            <svg width="15" height="11" viewBox="0 0 15 11"><rect x="4" width="11" height="7" fill="#222"/><rect y="3" width="4" height="4" fill="#222"/><circle cx="3" cy="9" r="2" fill="#222"/><circle cx="12" cy="9" r="2" fill="#222"/></svg>
            <span class="ahead">-</span>
            <svg width="9" height="13" viewBox="0 0 9 13"><path d="M4.5 13 1 6a4 4 0 1 1 7 0z" fill="#222"/><circle cx="4.5" cy="4.5" r="1.6" fill="#fff"/></svg>
            <span class="ahead">-</span>
          </div></td>
          <td>8:00 hrs</td><td>-</td>
        </tr>
        <tr class="empty"><td></td><td></td><td></td><td></td><td></td><td></td><td></td><td></td><td></td></tr>
      </tbody>
    </table>
  </section>

  <section class="abs panel" style="left:250px">
    <h3>Neque Porro</h3>
    <div class="map" role="img" aria-label="World map showing delivery regions"></div>
  </section>

  <section class="abs panel" style="left:808px">
    <h3>Neque Porro</h3>
    <svg class="chart" width="529" height="333" viewBox="808 779 529 333" font-family="Lato,sans-serif" font-size="14" font-weight="700" fill="#222">
      <path d="M862 800V1072H1290" fill="none" stroke="#d0d0d0"/>
      <path d="M872 915C900 870 920 838 946 836C990 834 1030 860 1054 880C1090 900 1120 905 1142 913C1150 930 1150 947 1155 947L1259 955C1275 965 1282 975 1287 987L1287 1072L872 1072Z" fill="#cfe2bb" fill-opacity=".85"/>
      <path d="M872 1022C890 995 905 976 922 976C950 976 980 996 1002 996C1015 996 1025 1043 1034 1043C1060 1043 1080 817 1105 817C1130 817 1140 1031 1157 1031C1180 1031 1220 805 1255 805L1287 810L1287 1072L872 1072Z" fill="#fdd37a" fill-opacity=".65"/>
      <g fill="#2f74b5">
        <circle cx="872" cy="915" r="2.5"/><circle cx="946" cy="836" r="2.5"/><circle cx="1054" cy="880" r="2.5"/><circle cx="1142" cy="913" r="2.5"/><circle cx="1155" cy="947" r="2.5"/><circle cx="1259" cy="955" r="2.5"/><circle cx="1287" cy="987" r="2.5"/>
        <circle cx="872" cy="1022" r="2.5"/><circle cx="922" cy="976" r="2.5"/><circle cx="1002" cy="996" r="2.5"/><circle cx="1034" cy="1043" r="2.5"/><circle cx="1105" cy="817" r="2.5"/><circle cx="1157" cy="1031" r="2.5"/><circle cx="1255" cy="805" r="2.5"/>
      </g>
      <g text-anchor="end">
        <text x="854" y="810">50</text><text x="854" y="862">40</text><text x="854" y="914">30</text><text x="854" y="966">20</text><text x="854" y="1018">10</text><text x="854" y="1070">0</text>
      </g>
      <g text-anchor="middle">
        <text x="877" y="1091">Jan</text><text x="932" y="1091">Feb</text><text x="989" y="1091">Mar</text><text x="1046" y="1091">Apr</text><text x="1104" y="1091">May</text><text x="1161" y="1091">Jun</text><text x="1215" y="1091">July</text><text x="1275" y="1091">Aug</text>
      </g>
    </svg>
  </section>

  <section class="abs panel" style="left:1366px">
    <h3>Neque Porro</h3>
    <div class="notes">
      <div class="note"><h4>Praesent eget facilisis</h4><p>Ut ornare aliquam leo nec condimentum molestie purus nibh finibus felis consectetur suscipit.</p></div>
      <div class="note"><h4>Praesent eget facilisis</h4><p>Ut ornare aliquam leo nec condimentum molestie purus nibh finibus felis consectetur suscipit.</p></div>
      <div class="note"><h4>Praesent eget facilisis</h4><p>Ut ornare aliquam leo nec condimentum molestie purus nibh finibus felis consectetur suscipit.</p></div>
    </div>
  </section>

</div>
</body>
</html>
```